Online business manager needs a website

I need a website designed and then coded. I am an online business manager serving a number of different industries providing administrative support to existing small businesses and helping solo practitioners get their new business up and running.

I didn't have a logo formally designed but have been using the attached avatar and wouldn't mind something that incorporated that.

The business doesn't have an official name, so I've just been using my name Lena Morvath, Online Business Manager or Lena Morvath, OBM. I've attached two documents that I have made previously for an example of content.

I would prefer the final site be in Wordpress.

Requirements
Must have
• A way to contact me, testimonials, list of services

```html
<!DOCTYPE html>
<html lang="en">
<head>
<meta charset="utf-8">
<title>Lena Morvath, OBM</title>
<link href="https://fonts.googleapis.com/css2?family=Dancing+Script:wght@600;700&family=Roboto:wght@400;500;700&display=swap" rel="stylesheet">
<style>
:root{
  --purple:#4b1c8c;
  --purple-deep:#3d1473;
  --purple-soft:#f7f2fc;
  --ink:#111;
  --text:#444;
  --muted:#666;
  --line:#e4dcef;
  --footer:#212121;
  --white:#fff;
}
*{box-sizing:border-box;margin:0;padding:0}
html,body{width:1200px;height:3442px;overflow:hidden}
body{position:relative;font-family:'Roboto',sans-serif;color:var(--text);background:var(--white)}
.abs{position:absolute}
.script{font-family:'Dancing Script',cursive;font-weight:700}
.accent{color:var(--purple)}
svg{display:block}

/* top bar */
.topbar{left:452px;top:0;width:748px;height:40px;background:var(--purple);clip-path:polygon(26px 0,100% 0,100% 100%,0 100%)}
.topbar .item{position:absolute;top:0;height:40px;display:flex;align-items:center;gap:12px;color:#fff;font-size:16px;white-space:nowrap}
.social-dots{position:absolute;top:14px;display:flex;gap:14px;left:600px}
.social-dots span{width:12px;height:12px;border-radius:50%;background:#fff}

/* header */
.logo{font-family:'Dancing Script',cursive;font-weight:700;font-size:33px;color:var(--ink);white-space:nowrap}
.nav{left:412px;top:70px;display:flex;gap:20px;font-size:14px;color:#333;white-space:nowrap}
.nav a{color:inherit;text-decoration:none}
.nav .active{color:var(--purple);font-weight:500}
.btn{display:flex;align-items:center;justify-content:center;gap:10px;background:var(--purple);color:#fff;font-weight:700;font-size:14px;border-radius:22px;text-transform:uppercase}
.login{left:969px;top:59px;width:119px;height:40px}

/* hero */
.hero{left:0;top:116px;width:1200px;height:656px;background:linear-gradient(90deg,#f7f5f2 0%,#efebe5 38%,#b9a58b 60%,#6d5a45 78%,#d9d4cc 100%)}
.welcome{left:108px;top:296px;font-size:34px;color:var(--ink)}
.hero-title{left:106px;top:352px;font-size:74px;line-height:80px;color:var(--ink);white-space:nowrap}
.start{left:108px;top:541px;width:153px;height:40px}

/* section headings */
.heading{width:1200px;left:0;text-align:center;font-size:44px;color:var(--ink)}

/* services */
.service{top:931px;width:234px;height:436px;border:1px solid var(--line);border-radius:117px;background:#fff;text-align:center}
.service.raised{box-shadow:0 12px 28px rgba(0,0,0,.14);border-color:transparent}
.service .photo{position:absolute;left:26px;top:20px;width:182px;height:182px;border-radius:50%}
.service h3{position:absolute;top:218px;left:0;width:100%;font-family:'Dancing Script',cursive;font-weight:700;font-size:21px;line-height:26px;color:var(--purple)}
.service ul{position:absolute;left:8px;width:218px;list-style:none;font-size:15px;color:#555;line-height:30px}

/* about */
.about{left:0;top:1461px;width:1200px;height:614px;background:var(--purple-soft)}
.about-photo{left:116px;top:1550px;width:424px;height:424px;border-radius:50%;border-left:6px solid var(--purple);border-bottom:6px solid var(--purple);background:linear-gradient(135deg,#e6e6e6,#c7b8a6 55%,#8a7767)}
.about-thumb{left:374px;top:1825px;width:160px;height:160px;border-radius:50%;border:4px solid #fff;background:linear-gradient(135deg,#b9a58a,#d9b98c 50%,#7b8a93)}
.about-text{left:620px;top:1628px;width:464px;font-size:15px;line-height:28px;text-align:justify;color:#333}
.learn{left:620px;top:1906px;width:154px;height:41px}

/* rates */
.rate{top:2238px;width:219px;height:255px;background:#fff;box-shadow:0 8px 30px rgba(0,0,0,.09)}
.rate .label{position:absolute;left:42px;top:38px;font-size:15px;color:#333}
.rate .price{position:absolute;left:42px;top:64px;font-family:'Dancing Script',cursive;font-weight:700;font-size:48px;color:var(--purple)}
.rate ul{position:absolute;left:42px;top:138px;list-style:none;font-size:15px;line-height:31px;color:#444}
.rate li{display:flex;align-items:center;gap:12px}

/* testimonials */
.love{left:0;top:2579px;width:1200px;height:467px;background:linear-gradient(135deg,#4d1c8f,#3f1478 60%,#4a1a88)}
.avatar{left:549px;top:2734px;width:102px;height:102px;border-radius:50%;border:3px solid #fff;background:linear-gradient(135deg,#b58a5e,#e5c7a0 50%,#8e4b3c)}
.client{left:0;top:2866px;width:1200px;text-align:center;color:#fff;font-weight:500;font-size:16px}
.quote{left:224px;top:2908px;width:752px;text-align:center;color:#fff;font-size:16px;line-height:26px}

/* footer */
.footer{left:0;top:3046px;width:1200px;height:396px;background:var(--footer)}
.foot-logo{left:110px;top:3114px;color:#fff}
.foot-social{left:160px;top:3192px;display:flex;gap:10px}
.foot-social span{width:30px;height:30px;border:1.5px solid #fff;border-radius:50%}
.col h4{color:#fff;font-size:17px;font-weight:500;margin-bottom:18px}
.col ul{list-style:none;font-size:14px;line-height:26px;color:#eee}
.contact-row{display:flex;gap:14px;margin-bottom:14px;color:#eee;font-size:14px;line-height:20px}
.contact-row b{display:block;font-size:12px;font-weight:700}
.rule{left:110px;top:3370px;width:980px;height:1px;background:#3a3a3a}
.copy{left:0;top:3396px;width:1200px;text-align:center;color:#eee;font-size:15px}
.totop{left:1109px;top:3341px;width:36px;height:36px;border-radius:50%;background:var(--purple);display:flex;align-items:center;justify-content:center}
</style>
</head>
<body>

<!-- top bar -->
<div class="abs topbar">
  <div class="item" style="left:101px">
    <svg width="16" height="12" viewBox="0 0 16 12"><rect width="16" height="12" rx="1.5" fill="#fff"/><path d="M1 1l7 5 7-5" stroke="#4b1c8c" stroke-width="1.6" fill="none"/></svg>
    lena.morvath@mailbox.example
  </div>
  <div class="item" style="left:400px">
    <svg width="14" height="14" viewBox="0 0 14 14"><rect width="14" height="14" rx="2" fill="#fff"/><path d="M4 3.2c.4 3.5 3.3 6.4 6.8 6.8l.8-1.6-2-1-.9.9c-1.2-.5-2.2-1.5-2.7-2.7l.9-.9-1-2z" fill="#4b1c8c"/></svg>
    555.210.4836
  </div>
  <div class="social-dots"><span></span><span></span><span></span><span></span></div>
</div>

<!-- header -->
<div class="abs logo" style="left:110px;top:48px">Lena Morvath,<span class="accent">OBM</span></div>
<nav class="abs nav">
  <a class="active">HOME</a><a>ABOUT ME</a><a>SERVICES</a><a>CONTACT ME</a><a>TESTIMONIALS</a><a>CONTACT US</a>
</nav>
<div class="abs btn login">Login
  <svg width="10" height="12" viewBox="0 0 10 12"><circle cx="5" cy="3" r="3" fill="#fff"/><path d="M0 12c0-4 2-5.5 5-5.5S10 8 10 12z" fill="#fff"/></svg>
</div>

<!-- hero -->
<div class="abs hero" role="img" aria-label="Smiling woman in a blazer working on a laptop in a bright office"></div>
<div class="abs script welcome">Welcome To</div>
<h1 class="abs script hero-title"><span class="accent">Lena Morvath,</span> Online<br>Business Manager</h1>
<div class="abs btn start">Get Started
  <svg width="14" height="14" viewBox="0 0 14 14"><circle cx="7" cy="7" r="7" fill="#fff"/><path d="M4 7h5M7 4.5 9.5 7 7 9.5" stroke="#4b1c8c" stroke-width="1.8" fill="none"/></svg>
</div>

<!-- services -->
<h2 class="abs script heading" style="top:840px">Our <span class="accent">Services</span></h2>

<div class="abs service" style="left:111px">
  <div class="photo" role="img" aria-label="Hands reviewing printed charts beside a laptop" style="background:linear-gradient(135deg,#d9d1c5,#9c8b78 60%,#5e5247)"></div>
  <h3>Virtual Assistance</h3>
  <ul style="top:248px"><li>Calendar Management</li><li>Email Management</li><li>Light Graphic Design</li><li>Data Entry</li></ul>
</div>
<div class="abs service raised" style="left:365px">
  <div class="photo" role="img" aria-label="Woman using a smartphone at a desk" style="background:linear-gradient(135deg,#c9c2bb,#8d7d70 55%,#4a3f38)"></div>
  <h3>Social Media &amp; Content<br>Managemen</h3>
  <ul style="top:266px"><li>Content Repurposing</li><li>Graphics Creation</li><li>Audiogram Creation</li><li>Search Engine Optimization</li></ul>
</div>
<div class="abs service" style="left:619px">
  <div class="photo" role="img" aria-label="Hand ticking a checklist over a laptop keyboard" style="background:linear-gradient(135deg,#7fa6c4,#2f5f86 55%,#173650)"></div>
  <h3>Finance Management</h3>
  <ul style="top:248px"><li>Create Invoices</li><li>Track Receivables</li><li>Analyze Expenses</li><li>Year Over Year Analytics</li></ul>
</div>
<div class="abs service" style="left:873px">
  <div class="photo" role="img" aria-label="Thoughtful man in a blue shirt at a laptop" style="background:linear-gradient(135deg,#f1f1f1,#9bb7d4 55%,#4a6d94)"></div>
  <h3>Business Management</h3>
  <ul style="top:262px;line-height:17px"><li>Creation of Operating<br>Procedures</li></ul>
  <ul style="top:302px"><li>Review of Website Strategy</li><li>Reporting and Analytics</li><li>Project Management</li></ul>
</div>

<!-- about -->
<section class="abs about"></section>
<div class="abs about-photo" role="img" aria-label="Woman in glasses working on a laptop"></div>
<div class="abs about-thumb" role="img" aria-label="Portrait of Lena Morvath"></div>
<h2 class="abs script" style="left:620px;top:1565px;font-size:44px;color:var(--ink)">About <span class="accent">Me</span></h2>
<p class="abs about-text">Hi! I'm so excited that you have chosen to explore my portfolio. Helping businesses achieve their goals is my passion, and I'm thrilled that with my assistance you will have more time for your own passion project. I thrive while working independently, which means you can be confident when leaving tasks for me. The type of work that lights me up is anything involving organization and/or spreadsheets. You need data analyzed that includes multiple nested if formulas? You have an overwhelming amountof email to sort through and appointments to book? I'm your gal!</p>
<div class="abs btn learn">Learn More
  <svg width="14" height="14" viewBox="0 0 14 14"><circle cx="7" cy="7" r="7" fill="#fff"/><path d="M4 7h5M7 4.5 9.5 7 7 9.5" stroke="#4b1c8c" stroke-width="1.8" fill="none"/></svg>
</div>

<!-- rates -->
<h2 class="abs script heading" style="top:2148px">Rates And <span class="accent">Packages</span></h2>

<svg width="0" height="0" style="position:absolute"><defs><symbol id="tick" viewBox="0 0 14 14"><circle cx="7" cy="7" r="7" fill="#4b1c8c"/><path d="M3.8 7.2 6 9.3 10.2 4.9" stroke="#fff" stroke-width="1.8" fill="none"/></symbol></defs></svg>

<div class="abs rate" style="left:127px">
  <div class="label">Hourly Rate</div><div class="price">$40</div>
  <ul><li><svg width="14" height="14"><use href="#tick"/></svg>For clients</li><li><svg width="14" height="14"><use href="#tick"/></svg>needing only</li><li><svg width="14" height="14"><use href="#tick"/></svg>occasional help</li></ul>
</div>
<div class="abs rate" style="left:369px">
  <div class="label">20 hours/month</div><div class="price">$700</div>
  <ul><li><svg width="14" height="14"><use href="#tick"/></svg>Includes one 15</li><li><svg width="14" height="14"><use href="#tick"/></svg>minute meeting</li><li><svg width="14" height="14"><use href="#tick"/></svg>per week</li></ul>
</div>
<div class="abs rate" style="left:612px">
  <div class="label">40 hours/month</div><div class="price">$1,300</div>
  <ul><li><svg width="14" height="14"><use href="#tick"/></svg>Includes one 30</li><li><svg width="14" height="14"><use href="#tick"/></svg>minute meeting</li><li><svg width="14" height="14"><use href="#tick"/></svg>per week</li></ul>
</div>
<div class="abs rate" style="left:855px">
  <div class="label">80 hours/month</div><div class="price">$2,400</div>
  <ul><li><svg width="14" height="14"><use href="#tick"/></svg>Includes one 60</li><li><svg width="14" height="14"><use href="#tick"/></svg>minute meeting</li><li><svg width="14" height="14"><use href="#tick"/></svg>per week</li></ul>
</div>

<!-- testimonials -->
<section class="abs love"></section>
<h2 class="abs script heading" style="top:2634px;color:#fff">Client Love</h2>
<div class="abs avatar" role="img" aria-label="Portrait of client Dana R."></div>
<div class="abs client">Dana R. Owner, Brightline Roofing</div>
<p class="abs quote">When it became apparent that a project would take more time than I had, Lena stepped up to take on the required research. She was thorough and timely; able to meet a last-minute 12-hour deadline. I would highly recommend Lena to assist with your next project.</p>

<!-- footer -->
<footer class="abs footer"></footer>
<div class="abs logo foot-logo">Lena Morvath,OBM</div>
<div class="abs foot-social"><span></span><span></span><span></span><span></span></div>

<div class="abs col" style="left:467px;top:3121px">
  <h4>Quick Links</h4>
  <ul><li>Home</li><li>About me</li><li>Services</li><li>Contact me</li><li>Testimonials</li><li>Contact Us</li></ul>
</div>
<div class="abs col" style="left:668px;top:3121px">
  <h4>About Company</h4>
  <ul><li>Legal Information</li><li>Terms &amp; Condition</li><li>Privacy Policy</li><li>Support</li><li>Site Map</li><li>FAQ</li></ul>
</div>
<div class="abs col" style="left:877px;top:3121px">
  <h4>Contact Us</h4>
  <div class="contact-row">
    <svg width="14" height="14" viewBox="0 0 14 14" style="margin-top:2px"><path d="M2 1.5c.4 5.5 4.9 10 10.5 10.5l1-2.6-3-1.3-1.2 1.2C7.6 8.6 5.4 6.4 4.7 4.7L5.9 3.5 4.6.5z" fill="#fff"/></svg>
    <div><b>Phone</b>555-304-7719</div>
  </div>
  <div class="contact-row">
    <svg width="15" height="11" viewBox="0 0 16 12" style="margin-top:4px"><rect width="16" height="12" rx="1.5" fill="#fff"/><path d="M1 1l7 5 7-5" stroke="#212121" stroke-width="1.6" fill="none"/></svg>
    <div><b>Email</b>hello@morvathobm.example</div>
  </div>
  <div class="contact-row">
    <svg width="12" height="15" viewBox="0 0 12 16" style="margin-top:2px;margin-left:2px"><path d="M6 0a6 6 0 0 1 6 6c0 4.5-6 10-6 10S0 10.5 0 6a6 6 0 0 1 6-6z" fill="#fff"/><circle cx="6" cy="6" r="2.2" fill="#212121"/></svg>
    <div><b>Location</b>New York, Denver, Los Angeles</div>
  </div>
</div>

<div class="abs totop">
  <svg width="12" height="8" viewBox="0 0 12 8"><path d="M1 7 6 2l5 5" stroke="#fff" stroke-width="2" fill="none"/></svg>
</div>
<div class="abs rule"></div>
<div class="abs copy">2023 Copyright - Lena Morvath,OBM &nbsp;| All Rights Reserved &nbsp;|</div>

</body>
</html>
```